New Company Business Card design

Looking for a corporate looking business card utilising my new logo design - the logo i would like embossed as one option and flat as another - simplistic but stylish - less is more - we are an import export business launching into the market - i would like a couple of options as main background - Grey or Black

```html
<!DOCTYPE html>
<html lang="en">
<head>
<meta charset="utf-8">
<title>Meridian Trade Partners – Business Card</title>
<link rel="stylesheet" href="https://fonts.googleapis.com/css2?family=Cinzel:wght@400;500&family=Arimo:wght@400&display=swap">
<style>
  :root {
    --backdrop: #676767;
    --card-grey: #6a6b70;
    --brand-blue: #1e76bb;
    --paper: #ffffff;
    --ink-light: #ffffff;
    --serif: "Cinzel", "Times New Roman", serif;
    --sans: "Arimo", Arial, sans-serif;
  }
  * { margin: 0; padding: 0; box-sizing: border-box; }
  html, body { width: 1200px; height: 802px; overflow: hidden; background: var(--backdrop); }
  .stage { position: relative; width: 1200px; height: 802px; }
  .card { position: absolute; top: 274px; width: 443px; height: 265px; overflow: hidden; }
  .card--front { left: 135px; background: var(--card-grey); }
  .card--back { left: 624px; background: var(--paper); display: flex; align-items: center; justify-content: center; }
  .front-field { position: absolute; inset: 0; }
  .contact-block { position: absolute; right: 26px; top: 0; text-align: right; color: var(--ink-light); }
  .holder-name { position: absolute; right: 0; top: 66px; white-space: nowrap; font-family: var(--serif); font-size: 18px; letter-spacing: 0.5px; }
  .holder-role { position: absolute; right: 0; top: 88px; white-space: nowrap; font-family: var(--sans); font-size: 13.5px; }
  .contact-list { position: absolute; right: 0; top: 141px; list-style: none; font-family: var(--sans); font-size: 13.5px; line-height: 16px; }
  .contact-list li { display: flex; justify-content: flex-end; align-items: center; gap: 4px; white-space: nowrap; }
  .contact-icon { width: 10px; height: 10px; flex: none; }
  .brand { display: flex; align-items: center; gap: 10px; }
  .brand-dot { width: 16px; height: 16px; border-radius: 50%; background: var(--brand-blue); }
  .brand-name { font-family: var(--serif); font-weight: 500; font-size: 20px; letter-spacing: 0.5px; color: var(--brand-blue); }
</style>
</head>
<body>
<main class="stage">
  <section class="card card--front" aria-label="Business card front">
    <svg class="front-field" width="443" height="265" viewBox="0 0 443 265" aria-hidden="true">
      <circle cx="330" cy="214" r="250" fill="var(--brand-blue)"/>
    </svg>
    <div class="contact-block">
      <p class="holder-name">MARCUS HALE</p>
      <p class="holder-role">Managing Director</p>
      <ul class="contact-list">
        <li>044-210 987 654
          <svg class="contact-icon" viewBox="0 0 10 10" aria-hidden="true"><path d="M1 3.5C1 2 3 1.5 5 1.5S9 2 9 3.5L7.5 4 7 3H3L2.5 4Z M2.5 5h5l1 3.5h-7z" fill="#fff"/></svg>
        </li>
        <li>044-210 987 654
          <svg class="contact-icon" viewBox="0 0 10 10" aria-hidden="true"><rect x="2.5" y="0.5" width="5" height="9" rx="0.8" fill="none" stroke="#fff" stroke-width="1"/></svg>
        </li>
        <li>hello@meridiantp.com
          <svg class="contact-icon" viewBox="0 0 10 10" aria-hidden="true"><rect x="0.5" y="2" width="9" height="6.5" fill="#fff"/><path d="M0.5 2 5 5.8 9.5 2" fill="none" stroke="var(--brand-blue)" stroke-width="0.8"/></svg>
        </li>
        <li>www.meridiantp.com
          <svg class="contact-icon" viewBox="0 0 10 10" aria-hidden="true"><circle cx="5" cy="5" r="4.5" fill="#fff"/><path d="M2 4c1 0 2 1 2 2s1 2 1 3M6 1.5c0 1 1 1.5 2 1.5" fill="none" stroke="var(--brand-blue)" stroke-width="0.9"/></svg>
        </li>
      </ul>
    </div>
  </section>

  <section class="card card--back" aria-label="Business card back">
    <div class="brand">
      <span class="brand-dot" aria-hidden="true"></span>
      <span class="brand-name">MERIDIAN TRADE PARTNERS</span>
    </div>
  </section>
</main>
</body>
</html>
```